New, modern business card for growing audiology practice

We need a new business card for our audiology practice. Our logo and website have recently changed (more modern) and we want our business cards to reflect this change.
We conduct hearing tests, perform earwax removals, and fit & dispense hearing aids to our patients. We are a family owned practice in which the owner is the one who works directly with the patient. I have attached logos in various formats to use, as well as two ideas I found on this website; as well as a scanned copy of our current logo. Good luck!

Industry/Entity Type

Business

Contact Information for Business Card

Company name: Tolvera Hearing Center
Provider name: Peter Wolstenby, Au.D. F/NSB
Phone number: (802) 683-5127
Address: 837 W. Lindell Ave. Brookvale, VT 05361
email: tolverahearing@postvane.com
website: tolverahearing.com

Colors
000000
aaaaaa
dbdbdb
cacaca
9bcb3c
afd23c
cadf82
b1b1b1

Requirements
Must have
• My card must include information in the "details" section. In the attached images, I found a few that I liked and I would like to model after - "brisky bouncin'" and "Sound Method Center".
• Must be horizontal.
• Must include logos provided. I uploaded them in various file formats and various ways.
• Must match logo font, if possible, if not, please get as close as you can.
Nice to have
• I really like the idea of having a color on one side with just the logo and company name and the contact information and provider name on the other side. I also really like the idea of having the main color dominating on the logo/company side with accent of that same color on the contact side of the card.
Should not have
• Must not be vertical.

```html
<!DOCTYPE html>
<html lang="en">
<head>
<meta charset="utf-8">
<title>Tolvera Hearing Center – Business Card</title>
<link rel="stylesheet" href="https://fonts.googleapis.com/css2?family=Arimo:wght@400;700&family=Saira+Semi+Condensed:wght@600&display=swap">
<style>
  :root {
    --page-bg: #3a3a3a;
    --card-bg: #1c1c1c;
    --card-edge: #111111;
    --brand-green: #9bcb3c;
    --text-light: #f2f2f2;
    --emboss: #4a4a4a;
  }
  * { box-sizing: border-box; margin: 0; padding: 0; }
  html, body {
    width: 799px;
    height: 1200px;
    overflow: hidden;
    background: var(--page-bg);
    font-family: "Arimo", Arial, sans-serif;
  }
  .canvas { position: relative; width: 799px; height: 1200px; }
  .card {
    position: absolute;
    left: 80px;
    width: 640px;
    height: 366px;
    background: var(--card-bg);
    border: 1px solid var(--card-edge);
    border-radius: 4px;
    box-shadow: 0 10px 24px rgba(0,0,0,0.45);
  }
  .card--front { top: 140px; }
  .card--back { top: 700px; }

  .front-mark {
    position: absolute;
    inset: 0;
    display: flex;
    align-items: center;
    justify-content: center;
    gap: 18px;
  }
  .front-mark__dot {
    width: 34px; height: 34px;
    border-radius: 50%;
    background: var(--emboss);
  }
  .front-mark__name {
    font-size: 30px;
    letter-spacing: 1px;
    color: var(--emboss);
    text-transform: uppercase;
    white-space: nowrap;
  }

  .brand-dot {
    position: absolute;
    left: 92px; top: 70px;
    width: 96px; height: 96px;
    border-radius: 50%;
    background: var(--brand-green);
  }
  .divider {
    position: absolute;
    left: 300px; top: 60px;
    width: 2px; height: 200px;
    background: var(--brand-green);
  }
  .wordmark {
    position: absolute;
    left: 40px; bottom: 40px;
    font-size: 27px;
    letter-spacing: 0.5px;
    color: var(--text-light);
    text-transform: uppercase;
    white-space: nowrap;
  }
  .provider { position: absolute; left: 330px; top: 74px; }
  .provider__name {
    font-family: "Saira Semi Condensed", "Arial Narrow", sans-serif;
    font-weight: 600;
    font-size: 21px;
    color: var(--brand-green);
    line-height: 1.1;
    white-space: nowrap;
  }
  .provider__title { margin-top: 5px; font-size: 13px; color: var(--text-light); }
  .contact {
    position: absolute;
    left: 330px; top: 150px;
    list-style: none;
    font-size: 14px;
    color: var(--text-light);
    line-height: 18px;
  }
  .contact__item { display: flex; align-items: flex-start; gap: 10px; white-space: nowrap; }
  .contact__icon {
    flex: 0 0 13px;
    width: 13px; height: 13px;
    margin-top: 2px;
    fill: var(--brand-green);
  }
  .contact__icon--line { fill: none; stroke: var(--brand-green); }
</style>
</head>
<body>
<main class="canvas">

  <section class="card card--front" aria-label="Card front">
    <div class="front-mark">
      <span class="front-mark__dot"></span>
      <span class="front-mark__name">Tolvera Hearing Center</span>
    </div>
  </section>

  <section class="card card--back" aria-label="Card back">
    <span class="brand-dot"></span>
    <span class="divider"></span>
    <p class="wordmark">Tolvera Hearing Center</p>

    <div class="provider">
      <p class="provider__name">Peter Wolstenby, Au.D. F/NSB</p>
      <p class="provider__title">Owner - Audiologist</p>
    </div>

    <ul class="contact">
      <li class="contact__item">
        <svg class="contact__icon" viewBox="0 0 16 16" aria-hidden="true"><path d="M8 0a5.5 5.5 0 0 0-5.5 5.5C2.5 10 8 16 8 16s5.5-6 5.5-10.5A5.5 5.5 0 0 0 8 0zm0 8a2.5 2.5 0 1 1 0-5 2.5 2.5 0 0 1 0 5z"/></svg>
        <span>837 W. Lindell Ave.<br>Brookvale, VT 05361</span>
      </li>
      <li class="contact__item">
        <svg class="contact__icon" viewBox="0 0 16 16" aria-hidden="true"><path d="M3.6 1.2l2.3 2.6c.4.4.4 1 0 1.4L4.6 6.5c.9 2 2.9 4 4.9 4.9l1.3-1.3c.4-.4 1-.4 1.4 0l2.6 2.3c.4.4.4 1 0 1.4l-1.4 1.4C11 17.6 -1.6 5 .8 2.6L2.2 1.2c.4-.4 1-.4 1.4 0z"/></svg>
        <span>(802) 683-5127</span>
      </li>
      <li class="contact__item">
        <svg class="contact__icon" viewBox="0 0 16 16" aria-hidden="true"><path d="M0 3h16v1.2L8 9 0 4.2z"/><path d="M0 5.8l8 4.8 8-4.8V13H0z"/></svg>
        <span>tolverahearing@postvane.com</span>
      </li>
      <li class="contact__item">
        <svg class="contact__icon contact__icon--line" viewBox="0 0 16 16" aria-hidden="true"><circle cx="8" cy="8" r="7" stroke-width="1.6"/><path d="M1 8h14M8 1c-3 3.5-3 10.5 0 14M8 1c3 3.5 3 10.5 0 14" stroke-width="1.3"/></svg>
        <span>www.tolverahearing.com</span>
      </li>
    </ul>
  </section>

</main>
</body>
</html>
```